Construction Company

Design a clutter free business card, it can be double-sided utilizing the logo for VKM Ltd simple with all relevant contact information.

Please also a letterhead design to function for the purposes of invoicing, all mail requirements, with header to be distinctive while the footer ties page together and incorporates all necessary information.

For now, please use generic / dummy text and when a winner is selected, I will disclose the contact information.

Hi Designers! Please read the updated brief which includes the design of a business card and letterhead. Thank you!

```html
<!DOCTYPE html>
<html lang="en">
<head>
<meta charset="utf-8">
<title>VKM Ltd – Business Card</title>
<link rel="stylesheet" href="https://fonts.googleapis.com/css2?family=Arimo:wght@400;700&display=swap">
<style>
  :root {
    --brand-blue: #023393;
    --brand-gold: #b79408;
    --gold-light: #d2b33a;
    --silver: #e6e0e2;
    --white: #ffffff;
    --stage: #ebe9e8;
  }
  * { box-sizing: border-box; margin: 0; padding: 0; }
  html, body {
    width: 1200px;
    height: 900px;
    overflow: hidden;
    background: var(--stage);
    font-family: "Arimo", Arial, sans-serif;
  }
  .business-card {
    position: absolute;
    left: 100px;
    top: 141px;
    width: 1000px;
    height: 618px;
    background: var(--brand-blue);
    overflow: hidden;
    color: var(--white);
    box-shadow: 0 10px 30px rgba(0,0,0,0.18);
  }
  .gold-panel {
    position: absolute;
    top: 0;
    left: 700px;
    width: 300px;
    height: 100%;
    background: var(--brand-gold);
  }
  .emblem-area {
    position: absolute;
    left: 404px;
    top: 14px;
    width: 592px;
    height: 592px;
    border-radius: 50%;
    background: radial-gradient(circle at center, var(--brand-gold) 0%, var(--gold-light) 45%, var(--silver) 78%, rgba(230,224,226,0) 100%);
  }
  .brand {
    position: absolute;
    left: 56px;
    top: 72px;
    display: flex;
    align-items: center;
    gap: 18px;
  }
  .brand-dot {
    width: 54px;
    height: 54px;
    border-radius: 50%;
    background: var(--brand-gold);
  }
  .brand-name {
    font-size: 84px;
    font-weight: 700;
    line-height: 1;
    color: var(--white);
    letter-spacing: 1px;
  }
  .person {
    position: absolute;
    left: 60px;
    top: 228px;
  }
  .person-name {
    font-size: 36px;
    font-weight: 700;
    color: var(--brand-gold);
    line-height: 1.1;
  }
  .person-role {
    font-size: 30px;
    font-weight: 400;
    line-height: 1.2;
  }
  .contact-list {
    position: absolute;
    left: 60px;
    top: 332px;
    list-style: none;
  }
  .contact-item {
    display: flex;
    align-items: center;
    height: 37px;
    font-size: 30px;
    line-height: 1;
  }
  .contact-icon {
    width: 27px;
    height: 27px;
    margin-right: 12px;
    fill: var(--brand-gold);
    flex: none;
  }
  .address {
    position: absolute;
    left: 59px;
    top: 498px;
    font-size: 30px;
    line-height: 37px;
    font-style: normal;
  }
</style>
</head>
<body>
  <main class="business-card">
    <div class="gold-panel"></div>
    <div class="emblem-area" role="img" aria-label="Large brand flower emblem in gold and silver"></div>

    <div class="brand">
      <span class="brand-name">VKM LTD</span>
      <span class="brand-dot"></span>
    </div>

    <div class="person">
      <p class="person-name">DANIEL HARPER</p>
      <p class="person-role">Managing Director</p>
    </div>

    <ul class="contact-list">
      <li class="contact-item">
        <svg class="contact-icon" viewBox="0 0 24 24" aria-hidden="true"><path d="M6.6 10.8a15.1 15.1 0 0 0 6.6 6.6l2.2-2.2a1 1 0 0 1 1-.25 11.4 11.4 0 0 0 3.6.57 1 1 0 0 1 1 1V20a1 1 0 0 1-1 1A17 17 0 0 1 3 4a1 1 0 0 1 1-1h3.5a1 1 0 0 1 1 1c0 1.25.2 2.450.57 3.57a1 1 0 0 1-.25 1z"/></svg>
        044-987 654 321
      </li>
      <li class="contact-item">
        <svg class="contact-icon" viewBox="0 0 24 24" aria-hidden="true"><path d="M7 1h10a2 2 0 0 1 2 2v18a2 2 0 0 1-2 2H7a2 2 0 0 1-2-2V3a2 2 0 0 1 2-2zm0 3v14h10V4zm5 15.2a1.2 1.2 0 1 0 0 2.4 1.2 1.2 0 0 0 0-2.4z"/></svg>
        044-765 432 198
      </li>
      <li class="contact-item">
        <svg class="contact-icon" viewBox="0 0 24 24" aria-hidden="true"><path d="M2 5h20v14H2zm2 2v.4l8 5.3 8-5.3V7zm0 2.8V17h16V9.8l-8 5.3z"/></svg>
        info@vkmbuild.com
      </li>
      <li class="contact-item">
        <svg class="contact-icon" viewBox="0 0 24 24" aria-hidden="true"><path d="M12 2a10 10 0 1 0 0 20 10 10 0 0 0 0-20zm6.9 6h-3a15.6 15.6 0 0 0-1.4-3.6A8 8 0 0 1 18.9 8zM12 4c.8 1.2 1.5 2.5 1.9 4h-3.8c.4-1.5 1.1-2.8 1.9-4zM4.3 14a8 8 0 0 1 0-4h3.4a16 16 0 0 0 0 4zm.8 2h3a15.6 15.6 0 0 0 1.4 3.6A8 8 0 0 1 5.1 16zm3-8h-3a8 8 0 0 1 4.4-3.6A15.6 15.6 0 0 0 8.1 8zM12 20c-.8-1.2-1.5-2.5-1.9-4h3.8c-.4 1.5-1.1 2.8-1.9 4zm2.3-6H9.7a14 14 0 0 1 0-4h4.6a14 14 0 0 1 0 4zm.2 5.6a15.6 15.6 0 0 0 1.4-3.6h3a8 8 0 0 1-4.4 3.6zm1.8-5.6a16 16 0 0 0 0-4h3.4a8 8 0 0 1 0 4z"/></svg>
        www.vkmbuild.com
      </li>
    </ul>

    <address class="address">
      17, Station Road, West End<br>
      40218, Northland
    </address>
  </main>
</body>
</html>
```